Business Card for Field Bloom-Eco Friendly Organic Clothing Brand

We are looking for an amazing business card for our eco friendly, organic clothing brand. We are thinking maybe a business card with a peel off sticker on the back, since our hanging clothing tag is a peel off sticker on the back. I will attach our hang tag so we can make sure we stay in line with our design. I've also attached a bag we are doing because I do like the scattered emblem look as well.

```html
<!DOCTYPE html>
<html lang="en">
<head>
<meta charset="utf-8">
<title>Field Bloom Business Card</title>
<link href="https://fonts.googleapis.com/css2?family=Lato:wght@400;700;900&display=swap" rel="stylesheet">
<style>
  :root {
    --backdrop-top: #2b2b2b;
    --backdrop-bottom: #050505;
    --card-front: #f3f3f3;
    --gold: #c9a13f;
    --gold-light: #efdc9e;
    --ink: #2e2e2e;
    --white: #ffffff;
  }
  * { margin: 0; padding: 0; box-sizing: border-box; }
  html, body { width: 1200px; height: 900px; overflow: hidden; }
  body {
    font-family: "Lato", sans-serif;
    background: linear-gradient(180deg, var(--backdrop-top) 0%, #1a1a1a 45%, var(--backdrop-bottom) 100%);
    position: relative;
  }
  .card {
    position: absolute;
    top: 184px;
    height: 490px;
    border-radius: 12px;
    overflow: hidden;
  }
  .card-front {
    left: 299px;
    width: 301px;
    background: var(--card-front);
    text-align: center;
    color: var(--ink);
  }
  .card-back {
    left: 645px;
    width: 305px;
    background: linear-gradient(180deg, var(--gold) 0%, #dcc071 22%, var(--gold-light) 45%, #e8d08a 65%, var(--gold) 88%, #c69c3a 100%);
    text-align: center;
    color: var(--white);
  }
  .front-brand {
    position: absolute;
    top: 70px;
    left: 0;
    width: 100%;
    display: flex;
    align-items: center;
    justify-content: center;
    gap: 10px;
    font-weight: 900;
    font-size: 30px;
    color: var(--gold);
    letter-spacing: 0.5px;
  }
  .brand-square {
    width: 18px;
    height: 18px;
    background: var(--gold);
  }
  .person-name {
    position: absolute;
    top: 246px;
    width: 100%;
    font-size: 24px;
    font-weight: 400;
    color: var(--gold);
    letter-spacing: 0.3px;
  }
  .person-title {
    position: absolute;
    top: 274px;
    width: 100%;
    font-size: 15px;
  }
  .contact-list {
    position: absolute;
    top: 311px;
    width: 100%;
    list-style: none;
    font-size: 15px;
    line-height: 20px;
  }
  .contact-list li { display: flex; align-items: center; justify-content: center; gap: 8px; }
  .contact-list svg { fill: var(--gold); }
  .address {
    position: absolute;
    top: 420px;
    width: 100%;
    font-size: 14.5px;
    line-height: 16px;
  }
  .back-brand {
    position: absolute;
    top: 322px;
    width: 100%;
    font-size: 44px;
    font-weight: 900;
    letter-spacing: 0.5px;
  }
  .back-url {
    position: absolute;
    top: 420px;
    width: 100%;
    font-size: 16px;
    letter-spacing: 0.3px;
  }
</style>
</head>
<body>
  <section class="card card-front" aria-label="Business card front">
    <div class="front-brand"><span class="brand-square"></span><span>Field Bloom</span></div>
    <h1 class="person-name">JOHN SMITH</h1>
    <p class="person-title">Managing Direcator</p>
    <ul class="contact-list">
      <li>
        <svg width="10" height="10" viewBox="0 0 10 10" aria-hidden="true"><path d="M1 3 Q5 0 9 3 L8 4.5 L6.5 3.8 L6.5 3 Q5 2.5 3.5 3 L3.5 3.8 L2 4.5 Z M2.5 5 L7.5 5 L8.5 9 L1.5 9 Z"/></svg>
        <span>823-456-7890</span>
      </li>
      <li>
        <svg width="10" height="8" viewBox="0 0 10 8" aria-hidden="true"><path d="M0 0 H10 V8 H0 Z M0.8 0.8 L5 4.2 L9.2 0.8 Z" fill-rule="evenodd"/></svg>
        <span>info@youremail.com</span>
      </li>
    </ul>
    <p class="address">1234, Address Goes Here<br>Country Name, 123456</p>
  </section>

  <section class="card card-back" aria-label="Business card back">
    <p class="back-brand">Field Bloom</p>
    <p class="back-url">www.fieldbloom.com</p>
  </section>
</body>
</html>
```